QVR business card

Need a business card for a company that provides instructional design and elearning development services. The website is here: http://quorvane.studio/

I'm attaching a current logo, as well as the old business card design. While I like to keep it clean, the old design is too simplistic for my liking. The only idea I want to reuse from the old design is placing industry jargon on the back of the card, just need a better way to present it. But if you have other ideas for the back--feel free to experiment.

Please use the colors complementary to the color we have on the website. Thank you!

```html
<!DOCTYPE html>
<html lang="en">
<head>
<meta charset="utf-8">
<title>QVR business card</title>
<link rel="stylesheet" href="https://fonts.googleapis.com/css2?family=Source+Sans+3:wght@400;600;700&display=swap">
<style>
  :root {
    --stage: #121212;
    --card-front: #f3f3f3;
    --teal: #11aeaa;
    --teal-deep: #06b1ae;
    --sand: #dccf8f;
    --ink: #1d1d1d;
    --white: #ffffff;
  }
  * { margin: 0; padding: 0; box-sizing: border-box; }
  html, body {
    width: 1200px; height: 900px; overflow: hidden;
    background: var(--stage);
    font-family: "Source Sans 3", "Myriad Pro", Arial, sans-serif;
  }
  .stage { position: relative; width: 1200px; height: 900px; }
  .card {
    position: absolute; top: 184px; width: 302px; height: 490px;
    border-radius: 14px; text-align: center;
    box-shadow: 0 2px 6px rgba(0,0,0,0.45);
  }
  .card-front { left: 299px; background: var(--card-front); }
  .card-back {
    left: 646px; width: 304px;
    background: linear-gradient(180deg, var(--teal-deep) 0%, #3cb9a8 30%, #a1c89c 62%, var(--sand) 100%);
    color: var(--white);
  }
  .wordmark {
    position: absolute; left: 0; right: 0;
    font-weight: 700; letter-spacing: 4px; line-height: 1;
  }
  .card-front .wordmark { top: 106px; font-size: 64px; color: var(--teal); }
  .card-back .wordmark { top: 366px; font-size: 58px; color: var(--white); }
  .holder-name {
    position: absolute; top: 337px; left: 0; right: 0;
    font-size: 17px; font-weight: 700; color: var(--teal);
  }
  .contact {
    position: absolute; top: 400px; left: 0; right: 0;
    list-style: none; font-size: 14px; line-height: 17.5px; color: var(--ink);
  }
  .contact .label { color: var(--teal); font-weight: 600; }
  .help-title {
    position: absolute; top: 40px; left: 0; right: 0;
    font-size: 22px; font-weight: 700; letter-spacing: 0.3px;
  }
  .services {
    position: absolute; top: 97px; left: 0; right: 0;
    list-style: none; font-size: 17.5px; font-weight: 600; line-height: 29.4px;
    letter-spacing: 0.2px;
  }
</style>
</head>
<body>
<main class="stage">
  <section class="card card-front" aria-label="Card front">
    <div class="wordmark">QVR</div>
    <p class="holder-name">Daniel Vorhees</p>
    <ul class="contact">
      <li><span class="label">Phone:</span> 555-014-2290</li>
      <li><span class="label">Email:</span> dvorhees@quorvane.studio</li>
      <li><span class="label">Website:</span> www.quorvane.studio</li>
    </ul>
  </section>
  <section class="card card-back" aria-label="Card back">
    <h2 class="help-title">HOW CAN WE HELP?</h2>
    <ul class="services">
      <li>MOBILE LEARNING SCORM</li>
      <li>INSTRUCTIONAL DESIGN LMS</li>
      <li>MOOCS ELEARNING HTML5</li>
      <li>ADULT LEARNING THEORY</li>
      <li>GAMIFICATION CLASSROOM</li>
      <li>XAPI BLENDED LEARNING</li>
    </ul>
    <div class="wordmark">QVR</div>
  </section>
</main>
</body>
</html>
```